logo & Business Card Design

BrightHaven Termite & Pest Control, I need a great logo, take my ideas and run with them!
I will use this in marketing and website so needs to be eye catching but professional

Target Market(s)

Resedintial & Business

Industry/Entity Type

Marketing

Contact Information for Business Card

Need front side with pertinent info & Logo; back side will have a 25% off initial services Coupon!

Font styles to use
Sans Serif

Colors
ec1f27
1b1b1b

Requirements
Must have
• Professional logo and style
Nice to have
• Raised lettering, black, red, white colors maybe? I'm flexible, but those colors go good on any background, vehicle, uniform, etc...
Should not have
• Cheesy

```html
<!DOCTYPE html>
<html lang="en">
<head>
<meta charset="utf-8">
<title>BrightHaven Termite &amp; Pest Control – Business Cards</title>
<link rel="stylesheet" href="https://fonts.googleapis.com/css2?family=Alegreya:wght@400;700&family=Lato:wght@400&display=swap">
<style>
  :root {
    --page-bg: #e9e6e2;
    --card-black: #0c0c0c;
    --card-charcoal: #1b1b1b;
    --ink-white: #f2f2f2;
    --ink-soft: #cfcfcf;
    --brand-red: #ec1f27;
  }
  * { margin: 0; padding: 0; box-sizing: border-box; }
  html, body {
    width: 1200px;
    height: 900px;
    overflow: hidden;
    background: var(--page-bg);
  }
  .canvas {
    position: relative;
    width: 1200px;
    height: 900px;
  }
  .card {
    position: absolute;
    width: 540px;
    height: 310px;
    border-radius: 4px;
    background:
      radial-gradient(ellipse at 55% 35%, var(--card-charcoal) 0%, var(--card-black) 70%);
    box-shadow: 0 14px 30px rgba(0,0,0,0.28);
    overflow: hidden;
  }
  .card--front { left: 60px; top: 150px; }
  .card--back { left: 600px; top: 440px; }

  .brand-mark {
    display: flex;
    align-items: center;
    gap: 8px;
    font-family: "Alegreya", serif;
    font-weight: 700;
    color: var(--ink-white);
    white-space: nowrap;
  }
  .brand-mark__dot {
    width: 12px;
    height: 12px;
    border-radius: 50%;
    background: var(--brand-red);
    flex: none;
  }
  .card--front .brand-mark {
    position: absolute;
    left: 0; right: 0;
    top: 112px;
    justify-content: center;
    font-size: 30px;
  }
  .card--front .brand-sub {
    position: absolute;
    left: 0; right: 0;
    top: 156px;
    text-align: center;
    font-family: "Alegreya", serif;
    font-weight: 700;
    font-size: 14px;
    color: var(--ink-white);
  }
  .tagline {
    position: absolute;
    left: 0; right: 0;
    bottom: 42px;
    text-align: center;
    font-family: "Lato", sans-serif;
    font-size: 14px;
    color: var(--ink-white);
    letter-spacing: 0.2px;
  }

  .card--back .brand-mark {
    position: absolute;
    right: 28px;
    top: 34px;
    font-size: 20px;
  }
  .card--back .brand-mark__dot { width: 9px; height: 9px; }

  .contact {
    position: absolute;
    left: 40px;
    top: 150px;
    font-family: "Alegreya", serif;
    color: var(--ink-soft);
  }
  .contact__name {
    font-weight: 700;
    font-size: 26px;
    color: var(--ink-white);
    line-height: 1.05;
  }
  .contact__role {
    font-size: 16px;
    margin-bottom: 30px;
  }
  .contact__line {
    font-size: 14.5px;
    line-height: 1.45;
    color: var(--ink-white);
    white-space: nowrap;
  }
</style>
</head>
<body>
<main class="canvas">

  <section class="card card--front" aria-label="Business card front">
    <div class="brand-mark">
      <span class="brand-mark__dot"></span>
      <span>BrightHaven</span>
    </div>
    <p class="brand-sub">Termite and Pest Control</p>
    <p class="tagline">"A Shield of protection For Your Home or Business"</p>
  </section>

  <section class="card card--back" aria-label="Business card back">
    <div class="brand-mark">
      <span class="brand-mark__dot"></span>
      <span>BrightHaven</span>
    </div>
    <div class="contact">
      <p class="contact__name">Daniel Reyes</p>
      <p class="contact__role">Managing Director</p>
      <p class="contact__line">1234, Address GoesHere, Country, 12345</p>
      <p class="contact__line">T: (044) 123 456 789&nbsp;&nbsp; F: (044) 123456789&nbsp; M: (044)123456789</p>
      <p class="contact__line">E: info@youremail.com&nbsp;&nbsp; www.yourweb.com</p>
    </div>
  </section>

</main>
</body>
</html>
```